New design for www.TrimTable.com

On TrimTable you can find & book your hairdresser. TrimTable is the biggest platform in the Netherlands.

- The design should be a responcive design
- Should be able to go global, should fit in perfectly between all the big booking platforms like stayvo, ridlo etc,
- Should have te result of more bookings. :)
- We are ‘only’ asking a beautiful design, not a technical solution.
- We need a homepage (https://trimtable.com/), search resultpage ((https://trimtable.com/kapper/amsterdam/#), salonpage (https://trimtable.com/kapper/vorden/lumo-for-hair/), about us page (https://trimtable.com/aboutus/), for the hairdresser info page (https://trimtable.com/kapper/), login/register page (https://trimtable.com/account/signin/).

- On the page of the hairdresser there is a dynamic part. The part where you create your appointment. Please take a look at this part too after you choose your treatment (behandeling), employee (medewerker), Date (datum) and time (tijd). The part that you see after this, is the part where you fill in your data as a consumer.

I've added more logo's but mostly we use the green color.

A few of our competitors: www.plumsalo.com, www.korifex.com

Target Market(s)

All consumers

Industry/Entity Type

Hair And Beauty

Number of Pages Required

5+ page

Font styles to use
Sans Serif

Colors
abd036
c3c3c3
757575

Requirements
Must have
• Responsive
• We did an A/B test with the homepage. It turns out that option B works better then option A (take a look at the uploaded pictures). So what we need on the homepage: The USP's with the green checkboxes, The search button needs to by dynamic (changes for example from light green to dark green so you can see you can click it) The call to action sentence Zoek & Vind je kapsalon, the searchfield and searchbutton should be seperated.
Nice to have
• The style that we like is the flat design style. The website should be simple, clean and it should feel a bit like a luxury thing. Because an appointment with the hairdresser can be a real treat and luxury moment for yourself.
• The luxury feeling and flat design that is in the www.ridlo.com website is really nice for example. But then it has to be a bit more light and not so black and dark.

```html
<!DOCTYPE html>
<html lang="en">
<head>
<meta charset="utf-8">
<title>TrimTable – Find &amp; book your hairdresser</title>
<link rel="stylesheet" href="https://fonts.googleapis.com/css2?family=Roboto:wght@300;400;500;700&display=swap">
<style>
:root{
  --green:#abd036;
  --green-dark:#8fb321;
  --grey-light:#c3c3c3;
  --grey:#757575;
  --ink:#3c3c3c;
  --dark:#4a4a4a;
  --darker:#262626;
  --white:#ffffff;
  --paper:#f4f4f4;
}
*{margin:0;padding:0;box-sizing:border-box}
html,body{width:1200px;height:2552px;overflow:hidden}
body{font-family:'Roboto',Arial,sans-serif;color:var(--ink);background:var(--white);position:relative}
section,header,footer{position:absolute;left:0;width:1200px}

/* Hero */
.hero{top:0;height:660px;overflow:hidden}
.hero-photo{position:absolute;inset:0;background:linear-gradient(100deg,#6b6259 0%,#9a8f84 35%,#d9d2c8 60%,#b8aea3 80%,#5e5650 100%)}
.site-header{top:0;height:80px;display:flex;justify-content:space-between;align-items:center;padding:0 24px}
.brand{display:flex;align-items:center;gap:10px;color:var(--white);font-size:26px;font-weight:500}
.brand-dot{width:28px;height:28px;border-radius:50%;background:var(--white)}
.account-links{color:var(--white);font-size:15px}
.account-links span{margin:0 8px}
.search-panel{position:absolute;left:220px;top:282px;width:760px;height:286px;background:rgba(40,40,40,.72);text-align:center;color:var(--white)}
.search-title{font-size:29px;font-weight:400;line-height:40px;margin-top:26px}
.search-row{display:flex;justify-content:center;gap:10px;margin-top:30px}
.search-field{display:flex;width:570px;height:58px;background:var(--white)}
.search-input{flex:1;display:flex;align-items:center;padding-left:20px;color:var(--grey);font-size:15px;text-align:left}
.search-select{width:160px;display:flex;align-items:center;justify-content:space-between;padding:0 14px;border-left:1px solid var(--grey-light);color:var(--grey);font-size:14px}
.search-button{width:120px;height:58px;background:var(--green);color:var(--white);font-size:18px;display:flex;align-items:center;justify-content:center}
.search-alt{font-size:28px;font-weight:300;margin-top:28px}
.search-alt span{margin:0 16px}
.slider-dots{position:absolute;top:628px;left:0;width:1200px;display:flex;justify-content:center;gap:10px}
.slider-dots i{width:10px;height:10px;border-radius:50%;background:rgba(255,255,255,.6)}
.slider-dots i:first-child{background:var(--white)}

/* Steps */
.steps{top:660px;height:440px;background:var(--paper)}
.section-title{text-align:center;color:var(--green);font-size:30px;font-weight:400}
.steps .section-title{margin-top:60px}
.step{position:absolute;top:130px;width:300px;text-align:center}
.step svg{display:block;margin:0 auto}
.step-label{font-size:18px;color:var(--ink);line-height:26px;margin-top:14px}
.step-arrow{position:absolute;top:215px}

/* App */
.app{top:1100px;height:510px;background:var(--dark);color:var(--white)}
.phone{position:absolute;left:150px;top:60px}
.app-copy{position:absolute;left:475px;top:90px;width:560px}
.app-copy h2{font-size:32px;font-weight:500;line-height:40px}
.app-copy h3{font-size:26px;font-weight:300;line-height:36px;margin-top:6px}
.app-copy p{font-size:14px;line-height:21px;color:#e0e0e0;margin-top:22px}
.app-button{display:inline-block;margin-top:28px;background:var(--green);color:var(--white);font-size:15px;padding:16px 26px}

/* Stats */
.stats{top:1610px;height:460px;background:var(--white)}
.stats-heading{text-align:center;font-size:19px;margin-top:100px;color:var(--ink)}
.stat{position:absolute;top:200px;width:200px;text-align:center}
.stat svg{display:block;margin:0 auto}
.stat-number{position:absolute;top:44px;left:0;width:200px;font-size:20px;color:var(--ink)}
.stat-label{font-size:16px;margin-top:26px;color:var(--ink)}

/* Subscribe */
.subscribe{top:2070px;height:180px;overflow:hidden}
.subscribe-photo{position:absolute;inset:0;background:linear-gradient(90deg,#f1f0ee 0%,#e6e3df 50%,#d8d2cb 80%,#efece9 100%)}
.subscribe-inner{position:absolute;top:40px;left:0;width:1200px;text-align:center}
.subscribe-inner h4{color:var(--green);font-size:24px;font-weight:400}
.subscribe-form{display:flex;justify-content:center;margin-top:20px}
.subscribe-input{width:320px;height:54px;background:var(--white);border:1px solid var(--grey-light);display:flex;align-items:center;padding-left:18px;color:var(--grey);font-size:15px}
.subscribe-go{width:64px;height:54px;border:1px solid var(--grey-light);border-left:0;background:var(--white);display:flex;align-items:center;justify-content:center}

/* Footer */
.site-footer{top:2250px;height:250px;background:var(--green);color:var(--white)}
.footer-col{position:absolute;top:36px}
.footer-col h5{font-size:14px;font-weight:500;letter-spacing:.5px;margin-bottom:14px}
.footer-col li{list-style:none;font-size:12px;line-height:22px}
.footer-col p{font-size:12px;line-height:18px}
.news-form{display:flex;margin-top:14px}
.news-input{width:150px;height:34px;background:var(--white);color:var(--grey);font-size:11px;display:flex;align-items:center;padding-left:10px}
.news-button{height:34px;padding:0 12px;background:var(--darker);font-size:11px;display:flex;align-items:center}
.social{display:flex;gap:10px;margin-top:16px}
.social i{width:30px;height:30px;border-radius:50%;background:rgba(255,255,255,.35)}
.bottom-bar{position:absolute;left:0;width:1200px;top:2500px;height:52px;background:var(--darker);color:#bdbdbd;font-size:12px;display:flex;align-items:center;justify-content:center}
.bottom-bar .to-top{position:absolute;right:30px}
</style>
</head>
<body>

<section class="hero">
  <div class="hero-photo" role="img" aria-label="Photo of a smiling woman at a hair salon"></div>
  <header class="site-header">
    <div class="brand"><span class="brand-dot"></span>TrimTable</div>
    <div class="account-links">Login<span>|</span>Register</div>
  </header>
  <div class="search-panel">
    <h1 class="search-title">The greatest hairdresser bookings site in the<br>Netherlands with 541 hairdressers.</h1>
    <div class="search-row">
      <div class="search-field">
        <div class="search-input">Zoek op plaats of postcode</div>
        <div class="search-select">All treatments
          <svg width="10" height="6" viewBox="0 0 10 6"><path d="M0 0h10L5 6z" fill="#757575"/></svg>
        </div>
      </div>
      <div class="search-button">Search</div>
    </div>
    <div class="search-alt">or search salon name.<span>|</span>Map</div>
  </div>
  <div class="slider-dots"><i></i><i></i><i></i><i></i><i></i></div>
</section>

<section class="steps">
  <h2 class="section-title">How does it work?</h2>

  <div class="step" style="left:115px">
    <svg width="180" height="210" viewBox="0 0 180 210">
      <path d="M90 205 C70 170 8 140 8 88 A82 82 0 0 1 172 88 C172 140 110 170 90 205Z" fill="#fff" stroke="#e2e2e2" stroke-width="2"/>
      <circle cx="90" cy="88" r="44" fill="none" stroke="#abd036" stroke-width="3"/>
      <circle cx="85" cy="83" r="14" fill="none" stroke="#abd036" stroke-width="4"/>
      <path d="M95 93l14 14" stroke="#abd036" stroke-width="5" stroke-linecap="round"/>
    </svg>
    <div class="step-label">Search &amp; Find Hairdresser</div>
  </div>
  <svg class="step-arrow" style="left:400px" width="30" height="20" viewBox="0 0 30 20"><path d="M2 16 Q12 4 24 8" fill="none" stroke="#abd036" stroke-width="3"/><path d="M20 2l8 6-9 5z" fill="#abd036"/></svg>

  <div class="step" style="left:450px">
    <svg width="180" height="210" viewBox="0 0 180 210">
      <path d="M90 205 C70 170 8 140 8 88 A82 82 0 0 1 172 88 C172 140 110 170 90 205Z" fill="#fff" stroke="#e2e2e2" stroke-width="2"/>
      <circle cx="90" cy="88" r="44" fill="none" stroke="#abd036" stroke-width="3"/>
      <rect x="70" y="70" width="40" height="28" rx="2" fill="none" stroke="#abd036" stroke-width="3"/>
      <path d="M62 104h56" stroke="#abd036" stroke-width="4" stroke-linecap="round"/>
    </svg>
    <div class="step-label">Book your appointment<br>online with 100% certainty</div>
  </div>
  <svg class="step-arrow" style="left:735px" width="30" height="20" viewBox="0 0 30 20"><path d="M2 16 Q12 4 24 8" fill="none" stroke="#abd036" stroke-width="3"/><path d="M20 2l8 6-9 5z" fill="#abd036"/></svg>

  <div class="step" style="left:785px">
    <svg width="180" height="210" viewBox="0 0 180 210">
      <path d="M90 205 C70 170 8 140 8 88 A82 82 0 0 1 172 88 C172 140 110 170 90 205Z" fill="#fff" stroke="#e2e2e2" stroke-width="2"/>
      <circle cx="90" cy="88" r="44" fill="none" stroke="#abd036" stroke-width="3"/>
      <circle cx="78" cy="102" r="7" fill="none" stroke="#abd036" stroke-width="3"/>
      <circle cx="102" cy="102" r="7" fill="none" stroke="#abd036" stroke-width="3"/>
      <path d="M83 96 L104 68 M97 96 L76 68" stroke="#abd036" stroke-width="3" stroke-linecap="round"/>
    </svg>
    <div class="step-label">Enjoy your new hairstyle</div>
  </div>
</section>

<section class="app">
  <svg class="phone" width="180" height="400" viewBox="0 0 180 400" role="img" aria-label="Smartphone showing the TrimTable app">
    <rect x="1" y="1" width="178" height="398" rx="24" fill="#f2f2f2" stroke="#cfcfcf" stroke-width="2"/>
    <rect x="12" y="56" width="156" height="288" fill="#111"/>
    <rect x="70" y="26" width="40" height="6" rx="3" fill="#bdbdbd"/>
    <circle cx="90" cy="372" r="14" fill="none" stroke="#bdbdbd" stroke-width="2"/>
    <rect x="66" y="130" width="48" height="48" fill="#abd036"/>
    <text x="90" y="222" text-anchor="middle" fill="#fff" font-family="Roboto, Arial, sans-serif" font-size="20" font-weight="500">TrimTable</text>
  </svg>
  <div class="app-copy">
    <h2>All the hairdressers of Netherlands in your pocket?</h2>
    <h3>Download the mobile APP and always find a place to make a good hangday of</h3>
    <p>Lorem Ipsum has been the industry's standard dummy text ever since the 1500s, when an unknown printer took a galley of type and scrambled it to make a type specimen book. It has survived not only five centuries, but also the leap into electronic typesetting, remaining essentially unchanged.</p>
    <span class="app-button">Download Mobile App</span>
  </div>
</section>

<section class="stats">
  <div class="stats-heading">Last appointment on October 13, 2015 at 17:57</div>

  <div class="stat" style="left:65px">
    <svg width="124" height="124" viewBox="0 0 124 124"><circle cx="62" cy="62" r="56" fill="none" stroke="#e6e6e6" stroke-width="8"/><circle cx="62" cy="62" r="56" fill="none" stroke="#abd036" stroke-width="8" stroke-dasharray="260 352" transform="rotate(-90 62 62)"/></svg>
    <div class="stat-number">541</div>
    <div class="stat-label">salons</div>
  </div>
  <div class="stat" style="left:295px">
    <svg width="124" height="124" viewBox="0 0 124 124"><circle cx="62" cy="62" r="56" fill="none" stroke="#e6e6e6" stroke-width="8"/><circle cx="62" cy="62" r="56" fill="none" stroke="#abd036" stroke-width="8" stroke-dasharray="230 352" transform="rotate(-90 62 62)"/></svg>
    <div class="stat-number">16 413</div>
    <div class="stat-label">Treatments for booking</div>
  </div>
  <div class="stat" style="left:512px">
    <svg width="124" height="124" viewBox="0 0 124 124"><circle cx="62" cy="62" r="56" fill="none" stroke="#e6e6e6" stroke-width="8"/><circle cx="62" cy="62" r="56" fill="none" stroke="#abd036" stroke-width="8" stroke-dasharray="300 352" transform="rotate(-90 62 62)"/></svg>
    <div class="stat-number">570648</div>
    <div class="stat-label">Agreements</div>
  </div>
  <div class="stat" style="left:730px">
    <svg width="124" height="124" viewBox="0 0 124 124"><circle cx="62" cy="62" r="56" fill="none" stroke="#e6e6e6" stroke-width="8"/><circle cx="62" cy="62" r="56" fill="none" stroke="#abd036" stroke-width="8" stroke-dasharray="210 352" transform="rotate(-90 62 62)"/></svg>
    <div class="stat-number">7160</div>
    <div class="stat-label">Hairdressers Booking</div>
  </div>
  <div class="stat" style="left:950px">
    <svg width="124" height="124" viewBox="0 0 124 124"><circle cx="62" cy="62" r="56" fill="none" stroke="#e6e6e6" stroke-width="8"/><circle cx="62" cy="62" r="56" fill="none" stroke="#abd036" stroke-width="8" stroke-dasharray="280 352" transform="rotate(-90 62 62)"/></svg>
    <div class="stat-number">26 498</div>
    <div class="stat-label">Reliable reviews</div>
  </div>
</section>

<section class="subscribe">
  <div class="subscribe-photo" role="img" aria-label="Soft photo of a woman with styled hair"></div>
  <div class="subscribe-inner">
    <h4>Nice TrimTable get tips? Subscribe!</h4>
    <div class="subscribe-form">
      <div class="subscribe-input">Wat is je emailadres?</div>
      <div class="subscribe-go"><svg width="24" height="14" viewBox="0 0 24 14"><path d="M0 7h20M14 1l7 6-7 6" fill="none" stroke="#3c3c3c" stroke-width="2"/></svg></div>
    </div>
  </div>
</section>

<footer class="site-footer">
  <div class="footer-col" style="left:90px">
    <h5>LINKS</h5>
    <ul>
      <li>Hairdresser Amsterdam</li>
      <li>For hairdressers</li>
      <li>About us</li>
      <li>Terms &amp; privacy</li>
      <li>Contact</li>
    </ul>
  </div>
  <div class="footer-col" style="left:300px;width:220px">
    <h5>ABOUT US</h5>
    <p>TrimTable helps you find and book the right hairdresser near you. Compare salons, read reviews and choose a time that suits you, day or night, always online.</p>
  </div>
  <div class="footer-col" style="left:580px;width:200px">
    <h5>GET IN TOUCH</h5>
    <p>Address: Lindelaan 14,<br>1012 AB Amsterdam</p>
    <p style="margin-top:12px">Phone: +31 20 555 0147</p>
    <p style="margin-top:12px">Email: info@trimtable.com</p>
  </div>
  <div class="footer-col" style="left:840px;width:260px">
    <h5>NEWSLETTER</h5>
    <p>Sign up for our newsletter and get the latest salon news.</p>
    <div class="news-form"><div class="news-input">Enter your email</div><div class="news-button">Subscribe</div></div>
    <div class="social"><i></i><i></i><i></i></div>
  </div>
</footer>

<div class="bottom-bar">
  Copyright © 2015 · All Rights Reserved
  <span class="to-top">▲</span>
</div>

</body>
</html>
```